Driver License Monitoring Application Marketing Website

We need a new web design for our web application. The product is called "RoadPermitGuard." We provide a driver license monitoring service to companies and local government bodies with driver fleets. Our current website is available at www.RoadPermitGuard-example.com.

I prefer a clean, single-page design with good SEO. Attached are some PDFs with data about the project.

Target Market(s)

Companies with driver fleets, local government.

Industry/Entity Type

Government

Coding

Coded - Design and coding required

Number of Pages Required

1 page

Colors
000000

Requirements
Must have
• Content from current www.RoadPermitGuard-example.com and attached PDFs.
Nice to have
• Prefer a simple Bootstrap or similar design for easy editing.
• Room for a simple video explanation of how the product works (we don't have an actual video yet)

```html
<!DOCTYPE html>
<html lang="en">
<head>
<meta charset="utf-8">
<title>RoadPermitGuard – Driver License Monitoring</title>
<link rel="stylesheet" href="https://fonts.googleapis.com/css2?family=Open+Sans:wght@300;400;600;700&family=Roboto:wght@300;400;500&display=swap">
<style>
:root{
  --red:#b3191f;
  --ink:#1a1a1a;
  --text:#555;
  --nav:#0d1620;
  --header:#ececec;
  --band:#f1f0ee;
  --footer:#2a2a2a;
  --white:#fff;
}
*{box-sizing:border-box;margin:0;padding:0}
html,body{width:862px;height:1200px;overflow:hidden;background:var(--white)}
body{position:relative;font-family:"Roboto",sans-serif;color:var(--text)}
.abs{position:absolute}
.site-header{left:0;top:0;width:862px;height:82px;background:var(--header);border-top:2px solid var(--red)}
.brand{left:72px;top:26px;font-family:"Open Sans",sans-serif;font-weight:700;font-size:20px;letter-spacing:.5px;color:var(--ink)}
.search{left:774px;top:31px}
.main-nav{left:0;top:82px;width:862px;height:38px;background:var(--nav)}
.main-nav a{position:absolute;top:14px;font-family:"Open Sans",sans-serif;font-size:9px;color:var(--white);text-decoration:none;letter-spacing:.2px}
.nav-sep{position:absolute;top:11px;height:16px;border-left:1px dotted #8a96a3}
.hero{left:0;top:120px;width:862px;height:311px;background:linear-gradient(180deg,#4a5a70 0%,#6b6470 40%,#7a5a4a 70%,#3d3a38 100%)}
.hero-shade{left:0;top:120px;width:862px;height:311px;background:rgba(30,30,45,.35)}
.hero-title{left:0;top:208px;width:862px;text-align:center;font-family:"Open Sans",sans-serif;font-weight:700;font-size:25px;line-height:34px;color:var(--white);letter-spacing:.3px}
.hero-sub{left:0;top:251px;width:862px;text-align:center;font-family:"Open Sans",sans-serif;font-size:14px;color:var(--white)}
.btn-red{left:385px;top:293px;width:93px;height:29px;background:var(--red);color:var(--white);font-family:"Open Sans",sans-serif;font-weight:700;font-size:10px;text-align:center;line-height:29px}
.intro-title{left:0;top:464px;width:862px;text-align:center;font-family:"Open Sans",sans-serif;font-weight:700;font-size:15px;color:var(--red)}
.intro-text{left:120px;top:495px;width:622px;text-align:center;font-weight:300;font-size:13px;line-height:21.6px;color:#666}
.btn-ghost{left:399px;top:551px;width:64px;height:23px;border:1px solid #ccc;border-radius:2px;font-family:"Open Sans",sans-serif;font-size:8px;color:#555;text-align:center;line-height:21px}
.industries{left:0;top:604px;width:862px;height:290px;background:var(--band)}
.industries-title{left:0;top:618px;width:862px;text-align:center;font-family:"Open Sans",sans-serif;font-weight:700;font-size:14px;line-height:20px;color:#444}
.industries-lead{left:0;top:651px;width:862px;text-align:center;font-size:8.5px;line-height:12px;color:#555}
.card-img{top:694px;width:170px;height:117px}
.card-title{top:822px;font-size:10.5px;color:var(--red)}
.card-text{top:842px;width:160px;font-size:7.5px;line-height:17px;color:#666}
.wwd-title{left:71px;top:921px;font-family:"Open Sans",sans-serif;font-weight:700;font-size:14.5px;color:#555}
.wwd-rule{left:71px;top:944px;width:53px;height:2px;background:#34506e}
.wwd-text{left:71px;width:240px;font-size:7px;line-height:13.6px;color:#7a7a7a}
.feature{top:954px;width:226px;height:147px;border:2px solid #fff;box-shadow:0 2px 6px rgba(0,0,0,.25)}
.feature-cap{position:absolute;left:0;bottom:0;width:100%;height:26px;background:rgba(0,0,0,.6);color:var(--white);font-family:"Open Sans",sans-serif;font-size:9px;text-align:center;line-height:26px}
.site-footer{left:0;top:1128px;width:862px;height:72px;background:var(--footer)}
.foot-links{left:72px;top:1146px;font-family:"Open Sans",sans-serif;font-size:7.5px;color:var(--white)}
.foot-copy{left:72px;top:1171px;font-family:"Open Sans",sans-serif;font-size:6.5px;color:var(--white)}
.social{top:1152px;width:20px;height:20px;border-radius:50%;background:var(--white)}
</style>
</head>
<body>
<header class="abs site-header"></header>
<div class="abs brand">RoadPermitGuard</div>
<svg class="abs search" width="12" height="12" viewBox="0 0 12 12"><circle cx="5" cy="5" r="3.8" fill="none" stroke="#c7c7c7" stroke-width="1.6"/><line x1="7.8" y1="7.8" x2="11" y2="11" stroke="#c7c7c7" stroke-width="1.8"/></svg>

<nav class="abs main-nav">
  <a style="left:74px">HOME</a><span class="nav-sep" style="left:128px"></span>
  <a style="left:157px">LICENSE MONITORING</a><span class="nav-sep" style="left:279px"></span>
  <a style="left:306px">ABOUT US</a><span class="nav-sep" style="left:380px"></span>
  <a style="left:405px">COMMERCIAL</a><span class="nav-sep" style="left:491px"></span>
  <a style="left:518px">GOVERNMENT</a><span class="nav-sep" style="left:608px"></span>
  <a style="left:634px">CONTACT</a><span class="nav-sep" style="left:701px"></span>
  <a style="left:730px">CLIENT LOGIN</a>
</nav>

<div class="abs hero" role="img" aria-label="City skyline by a harbour with docked yachts"></div>
<div class="abs hero-shade"></div>
<h1 class="abs hero-title">FLORIDA DRIVER LICENSE MONITORING</h1>
<div class="abs hero-sub">Monitor your fleet electronically. Get alerts by email and online.</div>
<div class="abs btn-red">SHOW MORE</div>
<svg class="abs" style="left:0;top:240px" width="862" height="120" viewBox="0 0 862 120">
  <circle cx="85" cy="24" r="12.5" fill="none" stroke="#fff" stroke-width="1.6"/>
  <polyline points="88,19 82,24 88,29" fill="none" stroke="#fff" stroke-width="1.6"/>
  <circle cx="776" cy="24" r="12.5" fill="none" stroke="#fff" stroke-width="1.6"/>
  <polyline points="773,19 779,24 773,29" fill="none" stroke="#fff" stroke-width="1.6"/>
  <circle cx="409" cy="110" r="2" fill="#fff"/>
  <circle cx="431" cy="110" r="7" fill="none" stroke="#fff" stroke-width="1.4"/>
  <circle cx="431" cy="110" r="2" fill="#fff"/>
  <circle cx="453" cy="110" r="2" fill="#fff"/>
</svg>

<h2 class="abs intro-title">TRACK YOUR FLEET FOR SAFETY AND PERFORMANCE</h2>
<p class="abs intro-text">Monitor your drivers electronically, twenty-four hours a day. How many of your drivers currently have a suspended license?&nbsp; The answer may surprise you.</p>
<div class="abs btn-ghost">READ MORE</div>

<section class="abs industries"></section>
<h2 class="abs industries-title">INDUSTRIES</h2>
<p class="abs industries-lead">At vero eos et accusamus et iusto odio dignissimos ducimus qui blanditiis praesentium dignissimos ducimus voluptatum...</p>

<div class="abs card-img" style="left:71px;background:linear-gradient(160deg,#3a4250,#7a7d80 55%,#2c2f33)" role="img" aria-label="Yellow delivery van on a curving road"></div>
<div class="abs card-img" style="left:255px;background:linear-gradient(180deg,#e0a92a,#c98b18 60%,#3a3020)" role="img" aria-label="Rear of a yellow school bus"></div>
<div class="abs card-img" style="left:439px;background:linear-gradient(120deg,#2a3b52,#6e8fb4 55%,#d8d8d2)" role="img" aria-label="Glass tower beside a capitol dome"></div>
<div class="abs card-img" style="left:623px;background:linear-gradient(180deg,#6f9ac4,#a9b8b0 50%,#274a6a)" role="img" aria-label="Offshore oil platform at sea"></div>

<div class="abs card-title" style="left:70px">Commercial Sector</div>
<div class="abs card-title" style="left:255px">School Districts</div>
<div class="abs card-title" style="left:438px">Government</div>
<div class="abs card-title" style="left:622px">Insurance Industry</div>
<div class="abs card-text" style="left:71px">Sed ut perspiciatis unde omnis iste natus quasi architecto vitae explicabo.</div>
<div class="abs card-text" style="left:255px">Sed ut perspiciatis unde omnis iste natus quasi architecto vitae explicabo.</div>
<div class="abs card-text" style="left:439px">Sed ut perspiciatis unde omnis iste natus quasi architecto vitae explicabo.</div>
<div class="abs card-text" style="left:623px">Sed ut perspiciatis unde omnis iste natus quasi architecto vitae explicabo.</div>

<h2 class="abs wwd-title">WHAT WE DO</h2>
<div class="abs wwd-rule"></div>
<p class="abs wwd-text" style="top:962px">The private sector is fraught with risk.&nbsp; Having an unlicensed or unqualified driver poses an extreme hazard for companies on the road. The consequences for unwittingly letting an unauthorized driver take the wheel can be disastrous.&nbsp; And when there is an accident, lawsuits, negative publicity, and even criminal prosecutions are likely.</p>
<p class="abs wwd-text" style="top:1041px">Managing driver license information is a demanding task.&nbsp; It's not enough to just request and file motor vehicle records. You have to review each and every one, and then determine whether or not any license activity warrants attention.</p>

<div class="abs feature" style="left:328px;background:linear-gradient(180deg,#5a4a3a,#c88a40 55%,#2a2420)" role="img" aria-label="Vintage van silhouetted at sunset">
  <div class="feature-cap">COMMERCIAL ( Private Sector )</div>
</div>
<div class="abs feature" style="left:566px;background:linear-gradient(180deg,#c9b48a,#8a6a48 50%,#3a2a20)" role="img" aria-label="Legislative chamber with rows of desks">
  <div class="feature-cap">GOVERNMENT ( Public Sector )</div>
</div>

<footer class="abs site-footer"></footer>
<div class="abs foot-links">HOME &nbsp;/&nbsp; LICENSE MONITORING &nbsp;/&nbsp; ABOUT US &nbsp;/&nbsp; CONTACT &nbsp;/&nbsp; CLIENT LOGIN</div>
<div class="abs foot-copy">COPYRIGHT © 2015 ROADPERMITGUARD &nbsp;|&nbsp; ALL RIGHTS RESERVED</div>
<span class="abs social" style="left:661px"></span>
<span class="abs social" style="left:688px"></span>
<span class="abs social" style="left:716px"></span>
<span class="abs social" style="left:743px"></span>
<span class="abs social" style="left:770px"></span>
</body>
</html>
```